Veluxa Bone & Motion Business Card

Need a business card using the logo provided. I want brand side of the card to be grey with the logo in the center of the card in white.

On the other side I leave to the designers

Target Market(s)

Personal Injury Attorneys

Industry/Entity Type

Medical

Contact Information for Business Card

Name, CEO. Cell Phone, (Marlowe, Address, Phone) (Homestead, Address, Phone) (Tallahassee, Address, Phone)

Colors

Designer to choose only greyscale colors for use in the design.

Requirements
Must have
• Logo by itself on one side

```html
<!DOCTYPE html>
<html lang="en">
<head>
<meta charset="utf-8">
<title>Veluxa Bone &amp; Motion Business Card</title>
<link href="https://fonts.googleapis.com/css2?family=Lato:wght@400;700&family=Quicksand:wght@500&display=swap" rel="stylesheet">
<style>
  :root {
    --backdrop: #2f2f30;
    --card-front-top: #8c8c8e;
    --card-front-bottom: #747476;
    --card-back-top: #6c6c6e;
    --card-back-bottom: #5d5d5f;
    --ink: #ffffff;
    --icon-ink: #5f5f61;
    --rule: #1f1f20;
  }
  * { margin: 0; padding: 0; box-sizing: border-box; }
  html, body {
    width: 1200px; height: 1200px; overflow: hidden;
    background: var(--backdrop);
  }
  .canvas { position: relative; width: 1200px; height: 1200px; }
  .card {
    position: absolute; left: 252px; width: 696px; height: 396px;
    color: var(--ink);
  }
  .card--brand {
    top: 155px;
    background: linear-gradient(160deg, var(--card-front-top), var(--card-front-bottom));
  }
  .card--contact {
    top: 609px;
    background: linear-gradient(160deg, var(--card-back-top), var(--card-back-bottom));
  }
  .wordmark {
    position: absolute; left: 0; right: 0; text-align: center;
    font-family: "Lato", sans-serif; font-weight: 700;
  }
  .wordmark__name { display: block; letter-spacing: 0.2em; padding-left: 0.2em; line-height: 1; }
  .wordmark__tag { display: block; letter-spacing: 0.2em; padding-left: 0.2em; line-height: 1; }
  .card--brand .wordmark { top: 142px; }
  .card--brand .wordmark__name { font-size: 68px; }
  .card--brand .wordmark__tag { font-size: 30px; margin-top: 8px; }
  .card--contact .wordmark { top: 43px; }
  .card--contact .wordmark__name { font-size: 43px; }
  .card--contact .wordmark__tag { font-size: 20px; margin-top: 5px; }

  .holder { position: absolute; left: 87px; top: 227px; }
  .holder__name {
    font-family: "Lato", sans-serif; font-weight: 700;
    font-size: 36px; letter-spacing: 0.12em; line-height: 1;
  }
  .holder__role {
    font-family: "Quicksand", sans-serif; font-weight: 500;
    font-size: 21px; line-height: 1; margin-top: 3px;
  }
  .divider {
    position: absolute; left: 336px; top: 197px; width: 1.5px; height: 136px;
    background: rgba(255,255,255,0.75);
  }
  .contact-list { position: absolute; left: 378px; top: 0; list-style: none; }
  .contact-item { position: absolute; left: 0; width: 300px; }
  .contact-item__icon {
    position: absolute; left: 0; width: 33px; height: 33px; border-radius: 50%;
    background: var(--ink);
  }
  .contact-item__icon svg { width: 33px; height: 33px; display: block; }
  .contact-item__text {
    position: absolute; left: 59px;
    font-family: "Quicksand", sans-serif; font-weight: 500;
    font-size: 15px; line-height: 17px; white-space: nowrap;
  }
  .contact-item__rule {
    position: absolute; left: 59px; width: 34px; height: 1.5px; background: var(--rule);
  }
</style>
</head>
<body>
<main class="canvas">

  <section class="card card--brand" aria-label="Brand side">
    <div class="wordmark">
      <span class="wordmark__name">VELUXA</span>
      <span class="wordmark__tag">BONE &amp; MOTION</span>
    </div>
  </section>

  <section class="card card--contact" aria-label="Contact side">
    <div class="wordmark">
      <span class="wordmark__name">VELUXA</span>
      <span class="wordmark__tag">BONE &amp; MOTION</span>
    </div>

    <div class="holder">
      <p class="holder__name">MARLOWE</p>
      <p class="holder__role">CEO</p>
    </div>

    <div class="divider"></div>

    <ul class="contact-list">
      <li class="contact-item" style="top:171px">
        <span class="contact-item__icon">
          <svg viewBox="0 0 33 33"><path d="M8 17 L16.5 9.5 L25 17 M11 15.5 V24 H15 V19.5 H18 V24 H22 V15.5" fill="none" stroke="var(--icon-ink)" stroke-width="2.2" stroke-linejoin="round"/></svg>
        </span>
        <p class="contact-item__text" style="top:-5px">Street Address Here<br>Singapore, 2222</p>
        <span class="contact-item__rule" style="top:37px"></span>
      </li>
      <li class="contact-item" style="top:218px">
        <span class="contact-item__icon">
          <svg viewBox="0 0 33 33"><rect x="9" y="11" width="15" height="11" fill="none" stroke="var(--icon-ink)" stroke-width="1.6"/><path d="M9 11 L16.5 17.5 L24 11 M9 22 L14.5 16 M24 22 L18.5 16" fill="none" stroke="var(--icon-ink)" stroke-width="1.4"/></svg>
        </span>
        <p class="contact-item__text" style="top:5px">urname@email.com</p>
        <span class="contact-item__rule" style="top:36px"></span>
      </li>
      <li class="contact-item" style="top:265px">
        <span class="contact-item__icon">
          <svg viewBox="0 0 33 33"><path d="M9 14 Q16.5 9 24 14 L22.5 16 L19.5 15 V13.5 H13.5 V15 L10.5 16 Z" fill="var(--icon-ink)"/><rect x="11" y="17" width="11" height="7" rx="1.5" fill="var(--icon-ink)"/><circle cx="16.5" cy="20.5" r="1.8" fill="#fff"/></svg>
        </span>
        <p class="contact-item__text" style="top:-1px">+18 5550 3140 2291<br>+18 5550 7826 4417</p>
        <span class="contact-item__rule" style="top:43px"></span>
      </li>
      <li class="contact-item" style="top:315px">
        <span class="contact-item__icon">
          <svg viewBox="0 0 33 33"><circle cx="16.5" cy="16.5" r="8" fill="none" stroke="var(--icon-ink)" stroke-width="1.5"/><ellipse cx="16.5" cy="16.5" rx="3.5" ry="8" fill="none" stroke="var(--icon-ink)" stroke-width="1.2"/><path d="M8.5 16.5 H24.5 M10 12.5 H23 M10 20.5 H23" stroke="var(--icon-ink)" stroke-width="1.1"/></svg>
        </span>
        <p class="contact-item__text" style="top:7px">www.websitename.com</p>
      </li>
    </ul>
  </section>

</main>
</body>
</html>
```